Lone Star Wetland Flora Stewardship Guild

We need to design the home page of this new website. We would like a fun website design for provides as a resource for members and information for potential members.
Please design so that we can see a portion of background on each side on the website.
I just need the final design files psd no coding needed.
Attached is their logo (colors are not 100% set in stone either so can mess with those as I did in the quick mockup attached)
Attached is a pdf newsletter they send out, you can get a feel for them and what they are about. The design is crappy and we are here to fix that going forward and we are starting with the website.
Here are some quick example websites (design style is open)
- I attached a quick mockup i did just for a content visual but by all means do what you want.
- http://www.brightpathleaders.example/
- http://www.civicunityhub.example/
- http://preview.webskinvault.example/show.php?cat=layouts&host=skinbazaar&temp=novaline
- http://www.meadowkeep.example/
- http://www.urbangleaners.example/
- http://www.projectcozyknit.example/
here are some of the other chapters website (pretty bad!)
and here are some of the others:
- http://www.dwrvcs.example/
- http://kwfg.example/
- http://www.blvcg.example/
Content Items that need to be included:
1. Logo
2. Menu - home, about, members, resources, events, membership, contact
3. Become a member - button or action
4. social links - chatterloop, workweave, clipstream
5. banner - that needs to explain their purpose "Promoting environmental stewardship through operations, research, education and outreach" (or this can be worked into the design)
6. Upcoming event (s)
7. Advertisement - members can place an ad on the website, this can be a placeholder for now
8. newsletter signup
9. advertise with us - this link can be in the footer
30-60 years of age, succesfull (household budgets of 120K+ men and women that live in texas.
Education

```html
<!DOCTYPE html>
<html lang="en">
<head>
<meta charset="utf-8">
<title>Lone Star Wetland Flora Stewardship Guild</title>
<link href="https://fonts.googleapis.com/css2?family=Ubuntu:wght@400;500;700&family=Raleway:wght@400;600&family=Open+Sans:wght@400;600&display=swap" rel="stylesheet">
<style>
:root{
  --nav-green:#17451f;
  --navy:#0d3b8c;
  --red:#d6475a;
  --panel:#4d4d4d;
  --text:#333;
  --footer:#262626;
  --footer-deep:#1c1c1c;
  --paper:#f6f6f6;
}
*{box-sizing:border-box;margin:0;padding:0}
html,body{width:1081px;height:1200px;overflow:hidden}
body{position:relative;font-family:Arial,Helvetica,sans-serif;color:var(--text);
  background:linear-gradient(#a8cfa4 0,#9cc59a 480px,#6f9c7c 700px,#4d7868 1000px,#3d6656 1066px)}
.backdrop{position:absolute;inset:0 0 134px 0}
.page{position:absolute;left:90px;top:0;width:900px;height:1066px;background:#fff}
.nav{position:absolute;top:0;left:0;width:900px;height:36px;background:var(--nav-green);display:flex;align-items:center;padding-left:13px}
.nav a{color:#fff;font-size:12px;text-decoration:none;padding:7px 12px;margin-right:10px;border-right:1px solid #2e6037}
.nav a.active{background:#111;border-radius:3px;border-right:none}
.nav .auth{position:absolute;right:45px;top:10px;color:#fff;font-family:Raleway,sans-serif;font-size:15px}
.banner{position:absolute;left:0;top:36px}
.brand{position:absolute;left:30px;top:54px;display:flex;align-items:center;gap:10px}
.brand .mark{width:34px;height:34px;background:var(--navy);border-radius:50%}
.brand span{font-family:Ubuntu,sans-serif;font-weight:700;font-size:15px;color:var(--navy);line-height:1.15;width:170px}
.social{position:absolute;left:519px;top:55px;display:flex;gap:8px}
.social i{width:32px;height:32px;border-radius:50%;display:block}
.join{position:absolute;left:689px;top:56px;width:188px;height:33px;background:var(--navy);color:#fff;font-family:Ubuntu,sans-serif;font-size:16px;display:flex;align-items:center;justify-content:center}
.tag1{position:absolute;left:526px;top:301px;width:313px;height:43px;background:var(--red);color:#fff;font-family:Ubuntu,sans-serif;font-weight:700;font-size:23px;display:flex;align-items:center;padding-left:13px;white-space:nowrap}
.tag2{position:absolute;left:225px;top:349px;width:616px;height:41px;background:var(--red);color:#fff;font-family:Raleway,sans-serif;font-size:19px;display:flex;align-items:center;padding-left:13px;white-space:nowrap;overflow:hidden}
.arrow{position:absolute;width:33px;height:33px}
.sidebar{position:absolute;left:11px;top:545px;width:246px;height:485px}
.sidebar h2{position:absolute;left:19px;top:20px;color:#fff;font-family:"Open Sans",sans-serif;font-weight:600;font-size:21px}
.field{position:absolute;left:13px;width:216px;height:26px;background:#fff;font-family:"Open Sans",sans-serif;font-size:12px;color:#555;padding:6px 8px}
.subscribe{position:absolute;left:46px;top:146px;width:150px;height:28px;background:var(--red);color:#fff;border-radius:2px;font-family:"Open Sans",sans-serif;font-size:15px;display:flex;align-items:center;justify-content:center}
.rule{position:absolute;left:6px;top:200px;width:234px;border-top:1px solid #6d6d6d}
.quote{position:absolute;left:19px;top:228px;width:211px;color:#fff;font-size:11px;line-height:16px;text-align:justify}
.quote p+p{margin-top:16px}
.welcome{position:absolute;left:294px;top:554px}
.welcome h1{font-family:Ubuntu,sans-serif;font-weight:700;color:var(--navy);font-size:28px;line-height:1.1}
.welcome h2{font-family:Raleway,sans-serif;font-weight:600;color:#111;font-size:22px;letter-spacing:1.5px}
.intro-photo{position:absolute;left:291px;top:632px;width:191px;height:148px;border:1px solid #bbb;padding:6px;background:#fff}
.intro{position:absolute;left:494px;top:632px;width:390px;font-size:11px;line-height:17px;color:#444}
.divider{position:absolute;left:285px;top:808px;width:600px;border-top:1px dotted #aaa}
.events{position:absolute;left:286px;top:828px;width:581px;height:208px;background:var(--paper);border:1px solid #ddd;border-bottom:4px solid #ccc;border-radius:4px}
.events h3{position:absolute;left:12px;top:8px;font-family:"Open Sans",sans-serif;font-weight:400;font-size:19px;letter-spacing:.8px;color:#222}
.event{position:absolute;left:12px;display:flex;gap:12px}
.event .thumb{width:42px;height:40px;border:2px solid #fff;box-shadow:0 0 1px #999}
.event p{font-size:9.5px;line-height:12px;width:450px;color:#222}
.event b{display:block}
.footer{position:absolute;left:0;top:1066px;width:1081px;height:104px;background:var(--footer);color:#fff}
.address{position:absolute;left:91px;top:40px;font-size:12.5px;line-height:18px;white-space:nowrap}
.fnav{position:absolute;left:295px;top:59px;font-size:11.5px;display:flex;white-space:nowrap}
.fnav span{padding:0 12px;border-left:1px solid #fff;line-height:11px}
.fnav span:first-child{border-left:none;padding-left:0}
.fbrand{position:absolute;left:858px;top:43px;display:flex;align-items:center;gap:8px;font-family:Ubuntu,sans-serif;font-weight:700;font-size:18px;color:#ddd}
.fbrand i{width:22px;height:22px;background:#ccc;border-radius:50%}
.copyright{position:absolute;left:0;top:1170px;width:1081px;height:30px;background:var(--footer-deep);color:#bbb;font-size:12px;text-align:center;line-height:30px}
</style>
</head>
<body>
<div class="backdrop" role="img" aria-label="Pond with floating water lily pads behind the page"></div>

<div class="page">
  <svg class="banner" width="900" height="520" viewBox="0 36 900 520">
    <defs>
      <linearGradient id="pond" x1="0" y1="0" x2="0" y2="1">
        <stop offset="0" stop-color="#4f6c5a"/><stop offset=".45" stop-color="#6c9a55"/><stop offset="1" stop-color="#3f5e4a"/>
      </linearGradient>
    </defs>
    <rect x="0" y="90" width="900" height="460" fill="url(#pond)" role="img" aria-label="Photo of lily pads and a white water lily in dark pond water"/>
    <path d="M0 36H900V112C700 116 520 128 330 152S80 172 0 176Z" fill="var(--paper)"/>
    <path d="M0 176C80 172 140 168 330 152S700 116 900 112" fill="none" stroke="#1c3f8c" stroke-width="5"/>
    <path d="M0 186C80 182 140 178 330 162S700 126 900 122" fill="none" stroke="var(--red)" stroke-width="14"/>
    <path d="M0 545C180 528 380 515 600 496S840 478 900 478V560H0Z" fill="#fff"/>
    <path d="M0 540C180 523 380 510 600 491S840 473 900 473" fill="none" stroke="var(--red)" stroke-width="16"/>
  </svg>

  <nav class="nav">
    <a class="active">HOME</a><a>ABOUT</a><a>MEMBERS</a><a>RESOURCES</a><a>EVENTS</a><a>MEMBERSHIP</a><a style="border-right:none">CONTACT</a>
    <span class="auth">Login &nbsp;/&nbsp; Register</span>
  </nav>

  <div class="brand"><i class="mark"></i><span>Lone Star Wetland Flora Stewardship Guild</span></div>
  <div class="social">
    <i style="background:#1f3f6d" aria-label="chatterloop"></i>
    <i style="background:#2ba3e0" aria-label="chirpwave"></i>
    <svg width="32" height="32" aria-label="news feed"><circle cx="16" cy="16" r="16" fill="#f39a1b"/><circle cx="11" cy="21" r="2" fill="#fff"/><path d="M10 14a8 8 0 0 1 8 8M10 9a13 13 0 0 1 13 13" stroke="#fff" stroke-width="2.2" fill="none"/></svg>
    <svg width="32" height="32" aria-label="email"><circle cx="16" cy="16" r="16" fill="#bdbdbd"/><rect x="9" y="11" width="14" height="10" fill="#fff"/><path d="M9 11l7 6 7-6" stroke="#bdbdbd" fill="none"/></svg>
  </div>
  <div class="join">BECOME A MEMBER</div>

  <div class="tag1">Promoting Environmental</div>
  <div class="tag2">Steward through Operations, Research, Education And Outreach</div>

  <div class="sidebar">
    <svg width="246" height="485" style="position:absolute;left:0;top:0">
      <path d="M0 0H246V470C170 450 80 452 0 468Z" fill="var(--panel)"/>
      <path d="M0 462C80 482 170 478 246 460" fill="none" stroke="var(--navy)" stroke-width="3"/>
    </svg>
    <h2>Newsletter sign up</h2>
    <div class="field" style="top:61px">Your Name</div>
    <div class="field" style="top:104px">Email Address</div>
    <div class="subscribe">Subscribe Now</div>
    <div class="rule"></div>
    <div class="quote">
      <p><b style="font-size:20px;line-height:8px">&ldquo;</b> Lorem ipsum dolor sit amet, consectetur adipisicing elit, sed do eiusmod tempor incididunt ut labore et dolore magna aliqua. Ut enim ad minim veniam, quis nostrud exercitation ullamco laboris nisi ut aliquip ex ea commodo..</p>
      <p>Consequat. Duis aute irure dolor in reprehenderit in voluptate velit esse cillum dolore eu fugiat nulla pariatur. sunt in culpa qui officia deserunt." <b style="font-size:20px;line-height:8px">&rdquo;</b></p>
    </div>
  </div>

  <div class="welcome">
    <h1>WELCOME TO</h1>
    <h2>Lone Star Wetland Flora Stewardship Guild</h2>
  </div>
  <div class="intro-photo"><div style="width:100%;height:100%;background:linear-gradient(120deg,#cfd8d4,#9fb49c 55%,#5f8a3f)" role="img" aria-label="Photo of a still pond edged with reeds"></div></div>
  <div class="intro">
    <p>Lorem ipsum dolor sit amet, consectetur adipiscing elit. Quisque dapibus accumsan orci, pretium eleifend arcu adipiscing eget. Fusce accumsan facilisis tincidunt. Phasellus tempor enim purus, vitae venenatis est. Ut imperdiet hendrerit pulvinar. Cras at tellus a enim condimentum mollis ut et tellus.</p>
    <p>Praesent ut accumsan facilisis tincidunt. Phasellus tempor enim purus, vitae venenatis est. Ut imperdiet hendrerit pulvinar. Cras at tellus a enim condimentum mollis ut et tellus. Mauris dolor magna, elementum eu dictum dui lectus, vel lacinia sem. Praesent commodo malesuada urna.</p>
  </div>
  <div class="divider"></div>

  <div class="events">
    <h3>Upcoming Event</h3>
    <div class="event" style="top:46px"><div class="thumb" style="background:linear-gradient(#9cc2dc,#6f9256)" role="img" aria-label="Event photo of a lake shore"></div><p><b>Lorem Ipsum is simply</b>dummy text of the printing and typesetting industry. the printing. &nbsp;dummy text of the printing and typesetting industry. the printing.</p></div>
    <div class="event" style="top:100px"><div class="thumb" style="background:linear-gradient(#9cc2dc,#6f9256)" role="img" aria-label="Event photo of a lake shore"></div><p><b>Lorem Ipsum is simply</b>dummy text of the printing and typesetting industry. the printing. &nbsp;dummy text of the printing and typesetting industry. the printing.</p></div>
    <div class="event" style="top:150px"><div class="thumb" style="background:linear-gradient(#9cc2dc,#6f9256)" role="img" aria-label="Event photo of a lake shore"></div><p><b>Lorem Ipsum is simply</b>dummy text of the printing and typesetting industry. the printing. &nbsp;dummy text of the printing and typesetting industry. the printing.</p></div>
  </div>
</div>

<svg class="arrow" style="left:75px;top:345px" viewBox="0 0 33 33"><circle cx="16.5" cy="16.5" r="16.5" fill="var(--navy)"/><path d="M21 10L11 16.5 21 23Z" fill="var(--red)"/></svg>
<svg class="arrow" style="left:970px;top:337px" viewBox="0 0 33 33"><circle cx="16.5" cy="16.5" r="16.5" fill="var(--navy)"/><path d="M12 10L22 16.5 12 23Z" fill="var(--red)"/></svg>

<footer class="footer">
  <div class="address">Cypress Bend Lane<br>P.O. Box 58, Ely, TX 75012</div>
  <div class="fnav"><span>HOME</span><span>ABOUT</span><span>MEMBERS</span><span>RESOURCES</span><span>EVENTS</span><span>MEMBERSHIP</span><span>CONTACT</span></div>
  <div class="fbrand"><i></i>LSWFSG</div>
</footer>
<div class="copyright">Copyright © 2014 Lswfsg. All Rights Reserved</div>
</body>
</html>
```